Voltara Growth Partners in need of a business card design

We need an innovative business card designed for a new company in Alberta, Canada. We assist organizations in improving performance by providing coaching and mentorship on how to promote and achieve organizational excellence. We teach senior leaders and their staff on how to continually improve performance; assist them in making sure the organization is innovative, competitive, and customer focused; support them in making sure the culture of the organization is also healthy, inclusive, and sustainable; and they are economically, socially, and environmentally responsible. We will do this by staying true to our company values of respect, excellence, integrity and trust.

Attached is our newly designed logo.

The team thought that having an inspirational quote similar to this one below would be a good addition somewhere on the card.

"Autograph your work with excellence.''

Target Market(s)

Private and public sector organizations. Once that are interested in being a Top 100 employer.

Industry/Entity Type

Business

Font styles to use
Sans Serif

Requirements
Must have
• 1. The business card must be double-sided.
2. Person's name and title
3. Email address
4. Phone number
5. Website (voltaragrowth.ca)
6. QR code
7. A quote somewhere on the front of the card: Autograph your work with excellence.
Nice to have

```html
<!DOCTYPE html>
<html lang="en">
<head>
<meta charset="utf-8">
<title>Voltara Growth Partners – Business Card</title>
<link rel="stylesheet" href="https://fonts.googleapis.com/css2?family=Roboto:wght@400;500;700&family=Dancing+Script:wght@500&display=swap">
<style>
  :root {
    --backdrop: #e4e0da;
    --card-black: #0e0e0f;
    --card-sheen: #2a2a2c;
    --white: #ffffff;
    --ink: #111111;
    --purple: #7d5fae;
    --blue: #2a8bcc;
    --green: #8cc63f;
    --quote-green: #a6d04a;
  }
  * { box-sizing: border-box; margin: 0; padding: 0; }
  html, body {
    width: 1200px;
    height: 913px;
    overflow: hidden;
    background: var(--backdrop);
  }
  .stage {
    position: relative;
    width: 1200px;
    height: 913px;
  }
  .card {
    position: absolute;
    width: 525px;
    height: 300px;
    border-radius: 6px;
    overflow: hidden;
    background: linear-gradient(150deg, var(--card-sheen) 0%, var(--card-black) 55%, #050505 100%);
    box-shadow: 0 14px 30px rgba(0, 0, 0, 0.28);
  }

  /* Front card */
  .card-front { left: 70px; top: 150px; }
  .front-brand {
    position: absolute;
    left: 70px;
    top: 170px;
    display: flex;
    align-items: center;
    gap: 16px;
  }
  .brand-dot {
    width: 34px;
    height: 34px;
    border-radius: 50%;
    background: var(--green);
    flex: none;
  }
  .brand-name {
    font-family: "Roboto", sans-serif;
    font-weight: 500;
    font-size: 34px;
    color: var(--white);
    letter-spacing: 0.5px;
    white-space: nowrap;
  }

  /* Back card */
  .card-back { left: 605px; top: 465px; }
  .quote {
    position: absolute;
    right: 26px;
    top: 22px;
    width: 270px;
    font-family: "Dancing Script", cursive;
    font-size: 19px;
    line-height: 1.35;
    color: var(--quote-green);
    text-align: center;
  }
  .quote-author {
    display: block;
    text-align: right;
    color: var(--white);
    font-size: 15px;
    margin-top: 2px;
  }
  .name-tab {
    position: absolute;
    left: 0;
    top: 126px;
    width: 290px;
    height: 60px;
    background: var(--white);
    border-radius: 0 22px 0 0;
    padding: 10px 0 0 60px;
    font-family: "Roboto", sans-serif;
    color: var(--ink);
  }
  .person-name { font-weight: 700; font-size: 19px; letter-spacing: 0.3px; }
  .person-title { font-weight: 400; font-size: 13px; margin-top: 2px; padding-left: 18px; }

  .contact-bar {
    position: absolute;
    left: 0;
    height: 34px;
    display: flex;
    align-items: center;
    border-radius: 0 17px 17px 0;
    font-family: "Roboto", sans-serif;
    font-size: 14px;
    color: var(--white);
  }
  .contact-bar svg { width: 18px; height: 18px; margin: 0 14px 0 70px; flex: none; }
  .bar-phone { top: 186px; width: 395px; background: var(--purple); }
  .bar-email { top: 220px; width: 425px; background: var(--blue); }
  .bar-web   { top: 254px; width: 450px; background: var(--green); }
</style>
</head>
<body>
<main class="stage">

  <section class="card card-front" aria-label="Card front">
    <div class="front-brand">
      <span class="brand-dot"></span>
      <span class="brand-name">Voltara Growth Partners</span>
    </div>
  </section>

  <section class="card card-back" aria-label="Card back">
    <p class="quote">“Every job is a<br>self-portrait<br>of the person who did it.<br>Autograph your work<br>with excellence.”
      <span class="quote-author">- Anonymous</span>
    </p>

    <div class="name-tab">
      <p class="person-name">Your Long Name</p>
      <p class="person-title">Titel</p>
    </div>

    <div class="contact-bar bar-phone">
      <svg viewBox="0 0 24 24" aria-hidden="true"><path fill="#fff" d="M6.6 10.8a15 15 0 0 0 6.6 6.6l2.2-2.2c.3-.3.7-.4 1-.2 1.1.4 2.3.6 3.6.6.6 0 1 .4 1 1V20c0 .6-.4 1-1 1A17 17 0 0 1 3 4c0-.6.4-1 1-1h3.5c.6 0 1 .4 1 1 0 1.3.2 2.5.6 3.6.1.3 0 .7-.2 1z"/></svg>
      <span>00.00.00.0000</span>
    </div>
    <div class="contact-bar bar-email">
      <svg viewBox="0 0 24 24" aria-hidden="true"><path fill="#fff" d="M2 5h20v14H2z"/><path fill="none" stroke="#2a8bcc" stroke-width="1.8" d="M2.5 5.5 12 13l9.5-7.5"/></svg>
      <span>yourname@yourwebsite.com</span>
    </div>
    <div class="contact-bar bar-web">
      <svg viewBox="0 0 24 24" aria-hidden="true"><g fill="none" stroke="#fff" stroke-width="1.8"><circle cx="12" cy="12" r="9"/><ellipse cx="12" cy="12" rx="4" ry="9"/><path d="M3 12h18M5 7h14M5 17h14"/></g></svg>
      <span>www.yourwebsite.com</span>
    </div>
  </section>

</main>
</body>
</html>
```